Upmarket Dessert Lounge needs a Business Card Design

We are an upmarket dessert lounge needing a business card to match our image.

We want something that is simple yet beautiful, feminine, classy, sophisticated and elegant. We want it to stand out and don't mind if it is bold.

The design should include our logo and colours of red or maroon with gold highlights. We don't mind if black is used.

Marlow & Quince

Target Market(s)

For those who like to indulge or treat themselves and give in to their temptations on good quality desserts.

Industry/Entity Type

Business

Requirements
Must have
• Must include our logo and our name

Marlow & Quince

M & Q

```html
<!DOCTYPE html>
<html lang="en">
<head>
<meta charset="utf-8">
<title>Marlow &amp; Quince — Business Card</title>
<link href="https://fonts.googleapis.com/css2?family=PT+Sans:wght@400;700&display=swap" rel="stylesheet">
<style>
  :root {
    --maroon: #7a1616;
    --maroon-dark: #6b1212;
    --cream: #f6d9a6;
    --gold: #f0c98a;
    --paper: #ffffff;
    --backdrop: #ebe6e0;
    --ink-soft: #5a1010;
  }
  * { box-sizing: border-box; margin: 0; padding: 0; }
  html, body { width: 1200px; height: 402px; overflow: hidden; }
  body {
    background: var(--backdrop);
    font-family: "PT Sans", Arial, sans-serif;
    position: relative;
  }
  .card {
    position: absolute;
    top: 56px;
    width: 513px;
    height: 291px;
    overflow: hidden;
    box-shadow: 0 2px 6px rgba(0,0,0,0.25);
  }
  .card--front { left: 65px; background: var(--paper); }
  .card--back { left: 627px; background: var(--maroon); }

  .brand-name {
    position: absolute;
    left: 0; right: 0;
    text-align: center;
    font-weight: 400;
    color: var(--maroon);
    font-size: 34px;
    letter-spacing: 1px;
    top: 58px;
  }
  .monogram {
    position: absolute;
    left: 0; right: 0;
    top: 88px;
    text-align: center;
    font-weight: 400;
    color: var(--cream);
    font-size: 84px;
    line-height: 1;
  }

  .holder {
    position: absolute;
    left: 0; right: 0;
    top: 176px;
    text-align: center;
    color: var(--maroon);
  }
  .holder__name { font-size: 17px; font-weight: 700; }
  .holder__title { font-size: 13px; font-weight: 400; color: var(--ink-soft); }
  .holder__address {
    margin-top: 8px;
    font-size: 13px;
    color: var(--ink-soft);
  }

  .contact-band {
    position: absolute;
    left: 0; top: 0;
    width: 513px; height: 291px;
  }
  .contacts {
    position: absolute;
    left: 0; right: 0;
    top: 250px;
    text-align: center;
    color: #fff;
    font-size: 12.5px;
    line-height: 19px;
  }
  .contacts__row { display: flex; justify-content: center; gap: 18px; }
  .contact { display: inline-flex; align-items: center; gap: 3px; }
  .contact svg { width: 11px; height: 11px; }
</style>
</head>
<body>

<section class="card card--front" aria-label="Business card front">
  <svg class="contact-band" viewBox="0 0 513 291" aria-hidden="true">
    <path d="M0 236 Q256 216 513 244" fill="none" stroke="var(--gold)" stroke-width="3"/>
    <path d="M0 242 Q256 222 513 250 L513 291 L0 291 Z" fill="var(--maroon)"/>
  </svg>

  <div class="brand-name">Marlow &amp; Quince</div>

  <div class="holder">
    <div><span class="holder__name">Your name,</span> <span class="holder__title">Title</span></div>
    <div class="holder__address">Street Name, City Name, State Zip Code</div>
  </div>

  <div class="contacts">
    <div class="contacts__row">
      <span class="contact">
        <svg viewBox="0 0 12 12"><circle cx="6" cy="6" r="5.3" fill="none" stroke="#fff" stroke-width="1"/><path d="M4 3.2 L5 3 L5.6 4.6 L4.9 5.2 Q5.6 6.6 6.8 7.2 L7.4 6.5 L9 7.1 L8.8 8.1 Q5 8.6 3.6 4.2 Z" fill="#fff"/></svg>555-218-4370
      </span>
      <span class="contact">
        <svg viewBox="0 0 12 12"><rect x="3" y="0.8" width="6" height="10.4" rx="1" fill="none" stroke="#fff" stroke-width="1.2"/><rect x="4.2" y="2.2" width="3.6" height="4" fill="#fff"/><circle cx="6" cy="9" r="0.8" fill="#fff"/></svg>555-218-4370
      </span>
      <span class="contact">
        <svg viewBox="0 0 12 12" fill="none" stroke="#fff" stroke-width="1"><circle cx="6" cy="6" r="5.2"/><ellipse cx="6" cy="6" rx="2.3" ry="5.2"/><path d="M0.8 6 H11.2 M1.8 3.3 H10.2 M1.8 8.7 H10.2"/></svg>www.marlow&amp;quince.com
      </span>
    </div>
    <div>info@marlow&amp;quince.com</div>
  </div>
</section>

<section class="card card--back" aria-label="Business card back">
  <div class="monogram">M &amp; Q</div>
</section>

</body>
</html>
```